Tall ridge firewood

It a new firewood outlet in Jindabyne nsw that will only sell top hardwood firewood (ironbark , red gum, grey gum, an box mix. I would like to see a web page the we can do order online payment for delivery. It will all so need to have photos of the firewood. I all so have logo for tall ridge firewood
Must have a modem look but easy to use I would like to see a black back ground of some sort.

Here are some other firewood web pages for ideas and firewood info
http://www.example-logpile.com.au
http://www.example-stackwood.com.au
http://www.example-splitlog.com.au
http://www.example-kendaltimber.com.au/firewood

Industry/Entity Type

Firewood

```html
<!DOCTYPE html>
<html lang="en">
<head>
<meta charset="utf-8">
<title>Tall Ridge Firewood</title>
<link rel="stylesheet" href="https://fonts.googleapis.com/css2?family=Oswald:wght@500;700&family=PT+Sans:wght@400;700&display=swap">
<style>
:root{
  --blue:#1a6fb8;
  --blue-dark:#145c9c;
  --ink:#4a4a4a;
  --muted:#666;
  --dark:#151515;
  --frame:#3a3a3a;
  --white:#fff;
  --light:#f2f2f2;
  --wood-a:#c89868;
  --wood-b:#8a5a34;
}
*{box-sizing:border-box;margin:0;padding:0}
html,body{width:957px;height:1200px;overflow:hidden;background:var(--white)}
body{font-family:"PT Sans",Tahoma,sans-serif;color:var(--ink);position:relative}
.abs{position:absolute}

/* header */
.site-header{position:absolute;left:0;top:0;width:957px;height:148px;background:var(--white);border-bottom:3px solid var(--blue)}
.brand{position:absolute;left:138px;top:52px;display:flex;align-items:center;gap:8px}
.brand-mark{width:22px;height:22px;border-radius:50%;background:var(--blue)}
.brand-name{font-family:"PT Sans",sans-serif;font-weight:700;font-size:17px;color:var(--blue);text-transform:uppercase;letter-spacing:.3px}
.topbar{position:absolute;left:354px;top:8px;display:flex;align-items:center;gap:14px;font-size:9px;color:var(--muted);text-transform:uppercase}
.topbar .item{display:flex;align-items:center;gap:5px}
.topbar .phone{font-family:"Oswald",sans-serif;font-weight:500;font-size:15px;color:#555}
.topbar .email{text-decoration:underline}
.topbar .cart-count{font-family:"Oswald",sans-serif;font-size:11px;color:#555}
.search{position:absolute;left:536px;top:37px;width:189px;height:19px;display:flex}
.search-field{flex:1;border:1px solid #ccc;border-right:0;font-size:9px;color:#999;padding:4px 6px}
.search-btn{width:20px;background:var(--blue);display:flex;align-items:center;justify-content:center}
.order-btn{position:absolute;left:746px;top:38px;width:84px;height:19px;background:linear-gradient(#f4f4f4,#d8d8d8);border-radius:3px;font-size:9px;font-weight:700;color:#222;display:flex;align-items:center;justify-content:center}
.main-nav{position:absolute;left:354px;top:99px;display:flex;height:27px}
.main-nav a{font-size:9.5px;font-weight:700;color:#555;text-decoration:none;text-transform:uppercase;padding:0 12.5px;display:flex;align-items:center}
.main-nav a.active{background:var(--blue);color:var(--white);padding:0 10px}

/* hero */
.hero{position:absolute;left:0;top:151px;width:957px;height:381px;background:var(--dark)}
.slider{position:absolute;left:128px;top:21px;width:701px;height:337px;background:var(--frame);border-radius:5px;padding:6px 7px}
.slide-photo{width:100%;height:100%;background:radial-gradient(ellipse at 60% 45%,var(--wood-a),var(--wood-b) 85%)}
.slide-caption{position:absolute;left:90px;top:142px;font-family:"Oswald",sans-serif;font-weight:700;line-height:1;text-transform:uppercase}
.slide-caption .l1{font-size:19px;color:var(--blue)}
.slide-caption .l2{font-size:27px;color:var(--white)}
.slide-arrow{position:absolute;top:152px;width:33px;height:33px;background:#222;border-radius:4px;display:flex;align-items:center;justify-content:center}
.slide-arrow.prev{left:24px}.slide-arrow.next{right:25px}

/* intro */
.section-title{font-family:"Oswald",sans-serif;font-weight:700;font-size:21px;color:#555}
.welcome{position:absolute;left:128px;top:556px;width:415px}
.welcome p{font-size:9.3px;line-height:11px;color:var(--muted);margin-top:9px}
.welcome .section-title{margin-bottom:2px}
.divider{position:absolute;left:586px;top:560px;width:1px;height:168px;background:#ddd}
.why{position:absolute;left:631px;top:556px;width:200px}
.why ul{list-style:none;margin-top:10px}
.why li{display:flex;gap:14px;align-items:flex-start;font-size:9px;line-height:11px;color:var(--muted);margin-bottom:13px;margin-left:-3px}
.tick{flex:none;width:16px;height:16px;background:#444;border-radius:3px;display:flex;align-items:center;justify-content:center;margin-top:1px}
.btn-blue{position:absolute;left:632px;top:709px;width:69px;height:19px;background:var(--blue);color:var(--white);font-size:9px;border-radius:3px;display:flex;align-items:center;justify-content:center}

/* products */
.products{position:absolute;left:128px;top:757px;width:701px;height:224px;background:var(--blue);border-radius:6px}
.products-head{height:46px;border-bottom:1px solid #3d86c6;display:flex;align-items:center;justify-content:space-between;padding:0 35px 0 36px}
.products-head .section-title{color:var(--white)}
.view-all{font-size:9px;font-weight:700;color:var(--white);text-decoration:underline}
.product-row{position:absolute;left:37px;top:63px;display:flex;gap:21px}
.product{width:141px;text-align:center;color:var(--white)}
.product-photo{height:101px;border:3px solid #e8e8e8;border-radius:5px}
.product-name{font-size:10.5px;margin-top:14px;text-transform:uppercase}
.product-price{font-family:"Oswald",sans-serif;font-weight:500;font-size:12px;margin-top:1px}
.carousel-arrow{position:absolute;top:90px}

/* footer */
.site-footer{position:absolute;left:0;top:1014px;width:957px;height:156px;background:var(--dark);border-bottom:3px solid var(--blue);color:var(--white)}
.footer-col{position:absolute;top:30px}
.footer-col h3{font-size:9px;font-weight:700;text-transform:uppercase;margin-bottom:8px}
.footer-col ul{list-style:none}
.footer-col li{font-size:8.5px;line-height:12.6px}
.footer-col li::before{content:"»";margin-right:6px}
.footer-sep{position:absolute;top:28px;width:1px;height:102px;background:#444}
.social{display:flex;gap:4px}
.social span{width:21px;height:21px}
.testimonial h3{font-size:13px;text-transform:none;margin-bottom:6px}
.testimonial p{font-size:8.7px;line-height:10.5px}
.testimonial .author{margin-top:10px}
.btn-light{margin-top:12px;width:70px;height:18px;background:linear-gradient(#fafafa,#d6d6d6);color:#222;font-size:8.5px;border-radius:3px;display:flex;align-items:center;justify-content:center}
.copyright{position:absolute;left:0;top:1173px;width:957px;height:27px;display:flex;align-items:center;justify-content:center;font-size:8.5px;color:#333;text-transform:uppercase}
</style>
</head>
<body>

<header class="site-header">
  <div class="brand"><span class="brand-mark"></span><span class="brand-name">Tall Ridge Firewood</span></div>
  <div class="topbar">
    <span class="item">
      <svg width="8" height="10" viewBox="0 0 8 10"><path d="M2 0 L3.5 2.5 2.5 3.5 Q3.5 6 5 7 L6 6 8 8 6.5 10 Q1 8 0 1Z" fill="#aaa"/></svg>
      Call us - <span class="phone">5550 318 204</span>
    </span>
    <span class="item">
      <svg width="10" height="7" viewBox="0 0 10 7"><rect x=".5" y=".5" width="9" height="6" fill="none" stroke="#bbb"/><path d="M.5 .5 5 4 9.5 .5" fill="none" stroke="#bbb"/></svg>
      Email us - <span class="email">info@tallridgefirewood.example</span>
    </span>
    <span class="item">
      <svg width="11" height="9" viewBox="0 0 11 9"><path d="M0 .5h2l1.5 5.5h6l1-4H3" fill="none" stroke="#aaa"/><circle cx="4" cy="8" r="1" fill="#aaa"/><circle cx="9" cy="8" r="1" fill="#aaa"/></svg>
      My cart - <span class="cart-count">0 item (s)</span>
    </span>
  </div>
  <div class="search">
    <span class="search-field">Find Firewood Products ..</span>
    <span class="search-btn"><svg width="10" height="10" viewBox="0 0 10 10"><circle cx="4" cy="4" r="3" fill="none" stroke="#fff" stroke-width="1.6"/><path d="M6.2 6.2 9 9" stroke="#fff" stroke-width="1.8"/></svg></span>
  </div>
  <div class="order-btn">ORDER ONLINE</div>
  <nav class="main-nav">
    <a class="active" href="#">Home</a><a href="#">About us</a><a href="#">Products</a><a href="#">Accessories</a><a href="#">Delivery</a><a href="#">Faq`s</a><a href="#">Contact us</a>
  </nav>
</header>

<section class="hero">
  <div class="slider">
    <div class="slide-photo" role="img" aria-label="Photo of a pile of cut hardwood logs"></div>
    <div class="slide-caption"><div class="l1">Top hardwood</div><div class="l2">Firewood</div></div>
    <div class="slide-arrow prev"><svg width="12" height="14" viewBox="0 0 12 14"><path d="M9 1 3 7l6 6" fill="none" stroke="#fff" stroke-width="3"/></svg></div>
    <div class="slide-arrow next"><svg width="12" height="14" viewBox="0 0 12 14"><path d="M3 1l6 6-6 6" fill="none" stroke="#fff" stroke-width="3"/></svg></div>
  </div>
</section>

<section class="welcome">
  <h2 class="section-title">Welcome to Tall Ridge Firewood</h2>
  <p>Lorem ipsum dolor sit amet, consectetur adipisicing elit, sed do eiusmod tempor incididunt ut labore et dolore magna aliqua. Ut enim ad minim veniam, quis nostrud exercitation ullamco laboris nisi ut aliquip ex ea commodo consequat. Duis aute irure dolor in reprehenderit in voluptate velit esse cillum dolore eu fugiat nulla pariatur. Excepteur sint occaecat cupidatat non proident, sunt in culpa qui officia deserunt mollit anim id est laborum.</p>
  <p>Lorem ipsum dolor sit amet, consectetur adipisicing elit, sed do eiusmod tempor incididunt ut labore et dolore magna aliqua. Ut enim ad minim veniam, quis nostrud exercitation ullamco laboris nisi ut aliquip ex ea commodo consequat. Duis aute irure dolor in reprehenderit in voluptate velit esse cillum dolore eu fugiat nulla pariatur. Excepteur sint occaecat cupidatat non proident, sunt in culpa qui officia deserunt mollit anim id est laborum.</p>
</section>
<div class="divider"></div>
<section class="why">
  <h2 class="section-title">Why Choose Us ?</h2>
  <ul>
    <li><span class="tick"><svg width="9" height="8" viewBox="0 0 9 8"><path d="M1 4l2.5 2.5L8 1" fill="none" stroke="#ddd" stroke-width="1.8"/></svg></span>Lorem ipsum dolor sit amet, consectetur adipisicing elit.</li>
    <li><span class="tick"><svg width="9" height="8" viewBox="0 0 9 8"><path d="M1 4l2.5 2.5L8 1" fill="none" stroke="#ddd" stroke-width="1.8"/></svg></span>Lorem ipsum dolor sit amet, consectetur adipisicing elit, sed do eiusmod tempor.</li>
    <li><span class="tick"><svg width="9" height="8" viewBox="0 0 9 8"><path d="M1 4l2.5 2.5L8 1" fill="none" stroke="#ddd" stroke-width="1.8"/></svg></span>Lorem ipsum dolor sit amet, consectetur adipisicing elit, sed do.</li>
  </ul>
</section>
<div class="btn-blue">READ MORE</div>

<section class="products">
  <div class="products-head"><h2 class="section-title">Our Products</h2><span class="view-all">VIEW ALL</span></div>
  <svg class="carousel-arrow" style="left:14px" width="10" height="50" viewBox="0 0 10 50"><path d="M9 1 1 25l8 24" fill="none" stroke="#cfe0f0" stroke-width="1.2"/></svg>
  <svg class="carousel-arrow" style="right:14px" width="10" height="50" viewBox="0 0 10 50"><path d="M1 1l8 24-8 24" fill="none" stroke="#cfe0f0" stroke-width="1.2"/></svg>
  <div class="product-row">
    <div class="product"><div class="product-photo" role="img" aria-label="Photo of split ironbark firewood" style="background:linear-gradient(#a0635a,#6b4a40 70%,#8a8a8a)"></div><div class="product-name">Ironbark</div><div class="product-price">$30.20 Only</div></div>
    <div class="product"><div class="product-photo" role="img" aria-label="Photo of split red gum firewood" style="background:linear-gradient(135deg,#8a3a2a,#c0503a 50%,#6a3a2a)"></div><div class="product-name">Red gum</div><div class="product-price">$30.20 Only</div></div>
    <div class="product"><div class="product-photo" role="img" aria-label="Photo of grey gum firewood logs" style="background:linear-gradient(135deg,#7a7e80,#5a5e62 60%,#8a8a88)"></div><div class="product-name">Grey gum</div><div class="product-price">$30.20 Only</div></div>
    <div class="product"><div class="product-photo" role="img" aria-label="Photo of box mix firewood burning in a fireplace" style="background:radial-gradient(ellipse at 50% 50%,#c0401a,#2a1a14 60%,#888 95%)"></div><div class="product-name">Box mix</div><div class="product-price">$30.20 Only</div></div>
  </div>
</section>

<footer class="site-footer">
  <div class="footer-col" style="left:129px">
    <h3>Navigation</h3>
    <ul><li>Home</li><li>About Us</li><li>Products</li><li>Accessories</li><li>Delivery</li><li>Faq`s</li><li>Contact Us</li></ul>
  </div>
  <div class="footer-sep" style="left:238px"></div>
  <div class="footer-col" style="left:281px">
    <h3>Products</h3>
    <ul><li>Ironbark</li><li>Red gum</li><li>Grey gum</li><li>Box mix</li></ul>
  </div>
  <div class="footer-sep" style="left:381px"></div>
  <div class="footer-col" style="left:424px">
    <h3>Follow us on</h3>
    <div class="social"><span style="background:#3b5a98"></span><span style="background:#2aa3de"></span><span style="background:#1a7ab8"></span><span style="background:#d8513e"></span></div>
  </div>
  <div class="footer-sep" style="left:565px"></div>
  <div class="footer-col testimonial" style="left:603px;width:230px;top:26px">
    <h3>Happy Client`s</h3>
    <p>Lorem ipsum dolor sit amet, consectetur adipisicing elit, sed do eiusmod tempor incididunt ut labore et dolore magna aliqua.</p>
    <p class="author"><b>Dale.</b> 15/06/13</p>
    <div class="btn-light">READ MORE</div>
  </div>
</footer>
<div class="copyright">Copyright ©&nbsp;<b>Tall Ridge Firewood</b>&nbsp;2013. All right reserved.</div>

</body>
</html>
```